Design a Website in Wordpress for an Australian Health Training Company in Health related courses

We require a WORDPRESS based Website (due to add on's we need to use for third party software) to replace our old site.
We offer national face to face delivery in medical reception, terminology and also administration.
The website will have around 6 pages and the ability to describe our main 6 courses (perhaps on the Courses page this may be tabs opening up to details for example?)
I have attached a previous sample of a Joomla site which was being developed (please do not feel you have to copy this - but I am just giving it as a sample - copying would be boring). But it gives an idea of look/feel and colours which may be suitable. Open to other ideas though.
I will provide some of the content, but would like the ability to finish the content myself.
Images and graphics are important. While a few medical photos re great - don't be tempted to us all pictures of doctors and nurses (although a couple would be good) - these are administrative courses so general corporate, eye catching visionary pictures of people in general are great. A medical type picture is also fine.
THE BOOKING system - will be via an ADD ON which will occur at the end of the project and is supplied by a third party software company (our student management system). This project will include up to 2 hours working with the Tech guys from the third party software to enable the ADD ON. If this ADD ON requires more time, we will pay hourly (although I do not expect it will).
Target Market(s)
Mostly a female market, many mature aged women target 25-45 yrs. Mixture of medical/health and corporate. Maybe a bit of mums returning to work and corporate inspiration.
Industry/Entity Type
It Company
Coding
Coded - Design and coding required
Number of Pages Required
5+ page
Requirements
Must have
- Wordpress
- Great graphics
- Interesting
- professional and clean
- Enquiry section (info Pak)
- Should have a University feel to it - Education
- Pages
- Home Page - About Us - Recruitment -Courses - Class Schedule - Traineeships Queensland Funding - Latest News Blog - Corporate Training- Contact us

```html
<!DOCTYPE html>
<html lang="en">
<head>
<meta charset="utf-8">
<title>Ashford Institute of Training</title>
<link href="https://fonts.googleapis.com/css2?family=Open+Sans:wght@400;600;700;800&family=Roboto+Slab:wght@400;700&display=swap" rel="stylesheet">
<style>
:root{
  --navy:#253559;
  --navy-dark:#1d2b4a;
  --orange:#f7923a;
  --grey:#8b8b8b;
  --light:#f1f1f1;
  --footer:#2b2b2b;
  --text:#3a3a3a;
  --white:#ffffff;
  --footer-mark:#4a5778;
}
*{box-sizing:border-box;margin:0;padding:0}
html,body{width:1200px;height:2941px;overflow:hidden}
body{font-family:"Open Sans",Arial,sans-serif;color:var(--text);background:var(--white);position:relative}
section,header,footer{position:absolute;left:0;width:1200px}
.abs{position:absolute}
.brand-name{font-family:"Open Sans",Arial,sans-serif;font-weight:700;color:var(--navy);line-height:1.2;white-space:nowrap}
.brand-mark{background:var(--navy)}

/* header */
.site-header{top:0;height:151px;border-top:6px solid var(--navy);background:var(--white)}
.logo{left:118px;top:22px;width:150px;display:flex;flex-direction:column;align-items:center;gap:10px}
.logo .brand-name{font-size:13px;text-align:center}
.logo .brand-mark{width:48px;height:48px}
.search{left:622px;top:20px;width:154px;height:42px;border:1px solid #cfcfcf;font-size:11px;color:#999;padding:13px 0 0 30px}
.search svg{position:absolute;left:12px;top:14px}
.btn{background:var(--orange);color:var(--white);font-weight:700;text-transform:uppercase;text-align:center;display:flex;align-items:center;justify-content:center;gap:8px}
.btn-info{left:790px;top:20px;width:136px;height:42px;font-size:14px}
.btn-enrol{left:933px;top:20px;width:136px;height:42px;font-size:13px;background:var(--navy)}
.main-nav{left:330px;top:92px;display:flex;font-size:11px;color:#222;align-items:center;height:40px}
.main-nav span{padding:0 9px;border-right:1px solid #ccc;line-height:1.2;text-align:center}
.main-nav span:last-child{border:none}
.main-nav .active{background:var(--navy);color:var(--white);padding:11px 14px;border:none}

/* hero */
.hero{top:151px;height:449px;background:linear-gradient(90deg,#cfd6de 0%,#e9edf1 30%,#dfe5ea 60%,#c8d2dc 100%)}
.hero-title{left:795px;top:205px;font-size:52px;font-weight:800;color:var(--white);line-height:1;letter-spacing:1px;text-shadow:0 1px 3px rgba(0,0,0,.25)}
.btn-more{left:800px;top:331px;width:150px;height:42px;font-size:15px}
.hero-arrow{top:203px;width:52px;height:52px;border-radius:50%;background:var(--navy);display:flex;align-items:center;justify-content:center}

/* courses */
.courses{top:600px;height:268px;background:var(--navy)}
.section-title-orange{color:var(--orange);font-weight:700;font-size:17px;text-align:center;letter-spacing:.5px}
.course-list{left:108px;top:95px;width:984px;display:flex}
.course{flex:1;text-align:center;color:var(--white);font-size:13px;font-weight:600;line-height:1.45;border-right:1px solid rgba(255,255,255,.18);height:130px}
.course:last-child{border:none}
.course.wide{flex:1.25}
.icon-circle{width:64px;height:64px;border-radius:50%;background:var(--orange);margin:0 auto 16px;display:flex;align-items:center;justify-content:center}

/* welcome */
.welcome{top:868px;height:372px}
.welcome-kicker{left:132px;top:30px;font-family:"Roboto Slab",Georgia,serif;font-size:14px;font-weight:700;color:var(--navy)}
.welcome-name{left:132px;top:54px;font-size:22px}
.welcome-copy{left:132px;top:118px;width:560px;font-size:11.5px;line-height:1.65}
.welcome-copy p{margin-bottom:12px}
.btn-read{left:132px;top:306px;width:120px;height:36px;font-size:12px}
.brand-panel{left:735px;top:66px;width:340px;height:274px;border:1px solid #e3e3e3;box-shadow:0 0 8px rgba(0,0,0,.06);display:flex;flex-direction:column;align-items:center;justify-content:center;gap:20px}
.brand-panel .brand-mark{width:96px;height:96px}
.brand-panel .brand-name{font-size:19px}

/* info pack + why */
.enquire{top:1240px;height:578px}
.info-side{left:0;top:0;width:600px;height:578px;background:var(--grey)}
.why-side{left:600px;top:0;width:600px;height:578px;background:linear-gradient(135deg,#2d3f66,#223256)}
.panel-title{font-family:"Roboto Slab",Georgia,serif;font-weight:700;font-size:17px;letter-spacing:.5px}
.info-side .panel-title{left:132px;top:44px;color:var(--white)}
.field{left:135px;width:385px;height:46px;background:var(--white);font-size:12px;color:#333;display:flex;align-items:center;padding-left:14px;gap:10px}
.field .chev{position:absolute;right:16px;top:15px}
.btn-send{left:135px;top:404px;width:385px;height:58px;font-size:24px;letter-spacing:1px}
.why-side .panel-title{left:48px;top:40px;color:var(--orange)}
.why-item{left:48px;width:440px;display:flex;gap:28px}
.why-item .icon-circle{width:54px;height:54px;margin:0;flex:none}
.why-item h4{color:var(--white);font-size:12px;font-weight:700;margin:4px 0 6px}
.why-item p{color:#d9deea;font-size:11px;line-height:1.55}

/* blog */
.blog{top:1818px;height:467px;background:var(--light)}
.blog .panel-title{left:132px;top:40px;color:var(--orange);font-size:18px}
.blog-nav{left:1030px;top:40px;display:flex;gap:10px}
.card{top:110px;width:220px;height:316px;background:var(--white)}
.card .date{position:absolute;left:85px;top:-20px;width:50px;height:50px;border-radius:50%;background:var(--white);text-align:center;font-size:16px;color:var(--orange);font-weight:600;line-height:1;padding-top:9px}
.card .date small{display:block;font-size:8px;color:#333;margin-top:3px}
.card .thumb{position:absolute;left:6px;top:22px;width:208px;height:150px}
.card h3{position:absolute;left:16px;top:188px;width:190px;font-size:11.5px;font-weight:700;color:var(--navy);line-height:1.35}
.card p{position:absolute;left:16px;top:226px;width:190px;font-size:10.5px;line-height:1.5;text-align:justify}
.card .more{position:absolute;left:16px;top:288px;font-size:9.5px;font-weight:700;color:var(--orange)}

/* testimonials */
.testimonials{top:2285px;height:335px;background:linear-gradient(180deg,#3a4d74,#2a3b61)}
.testimonials .panel-title{left:0;width:1200px;top:44px;text-align:center;color:var(--white)}
.title-rule{left:570px;top:78px;width:60px;height:3px;background:var(--orange)}
.quote-mark{left:150px;top:118px;font-family:Georgia,serif;font-size:90px;color:rgba(255,255,255,.7);line-height:1}
.quote-text{left:225px;top:124px;width:760px;text-align:center;color:var(--white);font-size:13px;line-height:1.7}
.author{top:244px;display:flex;align-items:center;gap:14px}
.avatar{width:48px;height:48px;border-radius:50%;background:linear-gradient(#d9c3b4,#b49480);border:3px solid var(--white)}
.author b{display:block;color:var(--white);font-size:12px}
.author small{color:#d9deea;font-size:10px}

/* footer */
.site-footer{top:2620px;height:275px;background:var(--footer);color:var(--white)}
.f-logo{left:120px;top:44px;width:180px;display:flex;flex-direction:column;align-items:center;gap:14px}
.f-logo .brand-name{color:var(--white);font-size:13px;text-align:center}
.f-logo .brand-mark{width:70px;height:70px;background:var(--footer-mark)}
.f-divider{left:338px;top:38px;width:1px;height:200px;background:#555}
.f-contact{left:362px;top:44px;font-size:11px;line-height:1.5}
.f-contact h5,.f-enquiry h5{font-size:12px;font-weight:700;margin-bottom:16px}
.f-contact b{display:block;font-size:11px}
.f-contact .grp{margin-bottom:14px}
.f-enquiry{left:635px;top:44px}
.f-field{position:absolute;left:0;width:212px;height:36px;background:var(--navy);color:var(--white);font-size:10px;padding:10px 12px}
.f-msg{position:absolute;left:220px;top:32px;width:215px;height:116px;background:var(--navy);font-size:10px;padding:10px 12px}
.btn-submit{left:982px;top:204px;width:88px;height:34px;font-size:12px}
.bottom-bar{top:2895px;height:46px;background:var(--orange);font-size:10px;color:#222}
.social{left:135px;top:12px;display:flex;align-items:center;gap:6px}
.social i{display:block;width:22px;height:22px;border-radius:50%;background:var(--navy)}
.social span{margin-right:4px}
.copyright{left:890px;top:16px}
</style>
</head>
<body>

<header class="site-header">
  <div class="abs logo">
    <div class="brand-name">ASHFORD INSTITUTE<br>OF TRAINING</div>
    <div class="brand-mark"></div>
  </div>
  <div class="abs search">
    <svg width="10" height="10" viewBox="0 0 10 10"><circle cx="4" cy="4" r="3" fill="none" stroke="#888" stroke-width="1.3"/><line x1="6.3" y1="6.3" x2="9.3" y2="9.3" stroke="#888" stroke-width="1.3"/></svg>
    SEARCH
  </div>
  <div class="abs btn btn-info">
    <svg width="16" height="16" viewBox="0 0 16 16"><circle cx="8" cy="8" r="7" fill="#fff"/><rect x="7" y="7" width="2" height="5" fill="#f7923a"/><rect x="7" y="4" width="2" height="2" fill="#f7923a"/></svg>
    Info Pack
  </div>
  <div class="abs btn btn-enrol">
    <svg width="12" height="16" viewBox="0 0 12 16"><rect x="4" y="1" width="3" height="9" rx="1.5" fill="#fff"/><rect x="2" y="7" width="9" height="8" rx="2" fill="#fff"/></svg>
    Enrol Now
  </div>
  <nav class="abs main-nav">
    <span class="active">Home</span>
    <span>About Us</span>
    <span>Recruitment</span>
    <span>Courses</span>
    <span>Class<br>Schedule</span>
    <span>Traineeships<br>Queensland Funding</span>
    <span>Latest<br>News Blog</span>
    <span>Corporate<br>Training</span>
    <span>Contact<br>us</span>
  </nav>
</header>

<section class="hero" role="img" aria-label="Photo of a smiling nurse in blue scrubs with stethoscope, medical colleagues blurred behind">
  <div class="abs hero-arrow" style="left:34px"><svg width="14" height="14" viewBox="0 0 14 14"><path d="M9 2 L4 7 L9 12" fill="none" stroke="#fff" stroke-width="2.4"/></svg></div>
  <div class="abs hero-arrow" style="left:1114px"><svg width="14" height="14" viewBox="0 0 14 14"><path d="M5 2 L10 7 L5 12" fill="none" stroke="#fff" stroke-width="2.4"/></svg></div>
  <h1 class="abs hero-title">MEDICAL<br>TRAINING</h1>
  <div class="abs btn btn-more">Read More <span>&raquo;</span></div>
</section>

<section class="courses">
  <h2 class="abs section-title-orange" style="left:0;width:1200px;top:42px">OUR COURSES</h2>
  <div class="abs course-list">
    <div class="course">
      <div class="icon-circle"><svg width="30" height="30" viewBox="0 0 30 30"><rect x="4" y="7" width="22" height="17" rx="2" fill="none" stroke="#fff" stroke-width="2"/><circle cx="12" cy="14" r="3" fill="#fff"/><rect x="7" y="18" width="10" height="3" fill="#fff"/><rect x="18" y="12" width="5" height="2" fill="#fff"/><rect x="18" y="16" width="5" height="2" fill="#fff"/></svg></div>
      Medical Reception &amp;<br>Terminology
    </div>
    <div class="course wide">
      <div class="icon-circle"><svg width="30" height="30" viewBox="0 0 30 30"><circle cx="15" cy="9" r="5" fill="#fff"/><path d="M5 27 Q5 16 15 16 Q25 16 25 27 Z" fill="#fff"/></svg></div>
      Cert III Business<br>Administration (Medical)
    </div>
    <div class="course">
      <div class="icon-circle"><svg width="32" height="30" viewBox="0 0 32 30"><path d="M16 27 L4 15 A6.5 6.5 0 0 1 16 6 A6.5 6.5 0 0 1 28 15 Z" fill="none" stroke="#fff" stroke-width="2.2"/><path d="M6 16 H12 L14 12 L17 20 L19 16 H26" fill="none" stroke="#fff" stroke-width="2"/></svg></div>
      Medical<br>Terminology
    </div>
    <div class="course">
      <div class="icon-circle"><svg width="32" height="26" viewBox="0 0 32 26"><rect x="2" y="4" width="28" height="18" rx="2" fill="none" stroke="#fff" stroke-width="2"/><g fill="#fff"><rect x="6" y="8" width="3" height="3"/><rect x="11" y="8" width="3" height="3"/><rect x="16" y="8" width="3" height="3"/><rect x="21" y="8" width="3" height="3"/><rect x="9" y="16" width="14" height="2.5"/></g></svg></div>
      Keyboard<br>and Typing
    </div>
    <div class="course">
      <div class="icon-circle"><svg width="30" height="30" viewBox="0 0 30 30"><circle cx="15" cy="15" r="11" fill="#fff"/><path d="M9 9 Q13 11 12 15 Q16 17 14 22 M18 7 Q20 11 23 12" fill="none" stroke="#f7923a" stroke-width="2"/></svg></div>
      Ashford<br>Online
    </div>
    <div class="course">
      <div class="icon-circle"><svg width="26" height="30" viewBox="0 0 26 30"><path d="M7 13 V9 A6 6 0 0 1 19 9 V13" fill="none" stroke="#fff" stroke-width="2.6"/><rect x="4" y="13" width="18" height="14" rx="2" fill="#fff"/></svg></div>
      <br>Confidentiality
    </div>
  </div>
</section>

<section class="welcome">
  <div class="abs welcome-kicker">WELCOME TO</div>
  <div class="abs brand-name welcome-name">ASHFORD INSTITUTE<br>OF TRAINING</div>
  <div class="abs welcome-copy">
    <p>Ashford is Australia’s Leading Provider of Educational, Training and Support Services for the Medical and Dental industry - enabling students to be immediately skilled and ‘Job Ready’ for a career in Health.</p>
    <p>Ashford is a Registered Training Organisation offering specialised Medical Administration Training in over 15 locations Australia wide. Ashford have trained thousands of students the required knowledge and skills to become successful health care administrators.</p>
    <p>Our unique Short Medical Reception and Terminology Course and our Full Qualification is Nationally Accredited and the go-to recognised qualification in industry.</p>
  </div>
  <div class="abs btn btn-read">Read More <span>&raquo;</span></div>
  <div class="abs brand-panel">
    <div class="brand-mark"></div>
    <div class="brand-name">ASHFORD INSTITUTE</div>
  </div>
</section>

<section class="enquire">
  <div class="abs info-side">
    <h2 class="abs panel-title">EMAIL ME AN INFO PACK</h2>
    <div class="abs field" style="top:90px"><svg width="11" height="11" viewBox="0 0 11 11"><circle cx="5.5" cy="3" r="2.6" fill="#333"/><path d="M1 11 Q1 6 5.5 6 Q10 6 10 11Z" fill="#333"/></svg>Name</div>
    <div class="abs field" style="top:154px"><svg width="12" height="10" viewBox="0 0 12 10"><rect x=".7" y=".7" width="10.6" height="8.6" fill="none" stroke="#333" stroke-width="1.2"/><path d="M1 1 L6 5.5 L11 1" fill="none" stroke="#333" stroke-width="1.2"/></svg>E mail</div>
    <div class="abs field" style="top:218px"><svg width="11" height="11" viewBox="0 0 11 11"><rect x=".7" y="2" width="8" height="8.3" fill="none" stroke="#333" stroke-width="1.2"/><path d="M4 7 L10 1" stroke="#333" stroke-width="1.5"/></svg>Course<svg class="chev" width="12" height="12" viewBox="0 0 12 12"><path d="M2 4 L6 8 L10 4" fill="none" stroke="#333" stroke-width="1.8"/></svg></div>
    <div class="abs field" style="top:282px"><svg width="11" height="11" viewBox="0 0 11 11"><circle cx="5.5" cy="5.5" r="5" fill="#333"/></svg>State</div>
    <div class="abs field" style="top:346px"><svg width="11" height="11" viewBox="0 0 11 11"><path d="M2 1 L4 1 L5 4 L3.5 5 Q5 7.5 6.5 8 L7.5 6.5 L10 7.5 L10 9.5 Q5 11 1 3Z" fill="#333"/></svg>Mobile</div>
    <div class="abs btn btn-send">SEND</div>
  </div>
  <div class="abs why-side">
    <h2 class="abs panel-title">WHY ASHFORD INSTITUTE ?</h2>
    <div class="abs why-item" style="top:88px">
      <div class="icon-circle"><svg width="24" height="24" viewBox="0 0 24 24"><rect x="2" y="10" width="5" height="11" fill="#fff"/><path d="M8 10 L12 3 Q14 3 14 6 L13 9 H20 Q22 9 21.5 11.5 L19.5 19.5 Q19 21 17 21 H8Z" fill="#fff"/></svg></div>
      <div><h4>QUALITY</h4><p>Ashford delivery quality, effective training facilitated by industry leaders. Just ask our students who rate us on average of 4.7 out of 5.</p></div>
    </div>
    <div class="abs why-item" style="top:176px">
      <div class="icon-circle"><svg width="26" height="26" viewBox="0 0 26 26"><circle cx="13" cy="13" r="8" fill="none" stroke="#fff" stroke-width="3" stroke-dasharray="4 2.3"/><circle cx="13" cy="13" r="3.5" fill="#fff"/></svg></div>
      <div><h4>EXPERIENCE</h4><p>Ashford is Australia’s largest and leading providers of nationally recognised training in health administration – training from over 17 locations Australia wide.</p></div>
    </div>
    <div class="abs why-item" style="top:270px">
      <div class="icon-circle"><svg width="24" height="24" viewBox="0 0 24 24"><path d="M12 2 L15 9 L22 9.5 L16.5 14 L18.5 21.5 L12 17.3 L5.5 21.5 L7.5 14 L2 9.5 L9 9Z" fill="#fff"/></svg></div>
      <div><h4>VALUE</h4><p>Our innovative teaching approach allows us to deliver exceptional training at affordable prices with no hidden extras.</p></div>
    </div>
    <div class="abs why-item" style="top:356px">
      <div class="icon-circle"><svg width="24" height="24" viewBox="0 0 24 24"><path d="M2 22 V12 L8 9 V12 L14 9 V4 H18 V22Z" fill="#fff"/></svg></div>
      <div><h4>INDUSTRY RECOGNISED</h4><p>Ashford work hand in hand with industry to develop our core programme and consolidate the programme annually to keep the programme fresh and relevant.</p></div>
    </div>
    <div class="abs why-item" style="top:458px">
      <div class="icon-circle"><svg width="24" height="24" viewBox="0 0 24 24"><g fill="#fff"><rect x="3" y="5" width="3" height="3"/><rect x="8" y="5" width="13" height="3"/><rect x="3" y="11" width="3" height="3"/><rect x="8" y="11" width="10" height="3"/><rect x="3" y="17" width="3" height="3"/><rect x="8" y="17" width="7" height="3"/></g></svg></div>
      <div><h4>GREAT JOB RESULTS</h4><p>Ashford students get jobs! Our focus is to create job-ready students who are mentored to achieve their goals. Ashford also provide a recruitment service for industry and graduates.</p></div>
    </div>
  </div>
</section>

<section class="blog">
  <h2 class="abs panel-title">LATEST BLOG</h2>
  <div class="abs blog-nav">
    <svg width="14" height="16" viewBox="0 0 14 16"><path d="M10 2 L4 8 L10 14" fill="none" stroke="#222" stroke-width="2.4"/></svg>
    <svg width="14" height="16" viewBox="0 0 14 16"><path d="M4 2 L10 8 L4 14" fill="none" stroke="#222" stroke-width="2.4"/></svg>
  </div>
  <article class="abs card" style="left:132px">
    <div class="date">25<small>JAN</small></div>
    <div class="thumb" role="img" aria-label="Photo of two medical staff reviewing a clipboard" style="background:linear-gradient(135deg,#cfe0ea,#9db7c7)"></div>
    <h3>Short Course Medical Reception Training,</h3>
    <p>The Ashford Medical Receptionist Training program is geared towards gaining employment and as part...</p>
    <div class="more">READ MORE</div>
  </article>
  <article class="abs card" style="left:368px">
    <div class="date">14<small>JUNE</small></div>
    <div class="thumb" role="img" aria-label="Photo of a doctor examining a brain scan on a tablet" style="background:linear-gradient(135deg,#3b4450,#14181d)"></div>
    <h3>Contrary to popular belief, Lorem Ipsum is not.</h3>
    <p>The Ashford Medical Receptionist Training program is geared towards gaining employment and as part...</p>
    <div class="more">READ MORE</div>
  </article>
  <article class="abs card" style="left:604px">
    <div class="date">13<small>FEB</small></div>
    <div class="thumb" role="img" aria-label="Photo of a patient monitor screen in a hospital ward" style="background:linear-gradient(135deg,#2c3a44,#5a7382)"></div>
    <h3>The standard chunk of Lorem Ipsum used since.</h3>
    <p>The Ashford Medical Receptionist Training program is geared towards gaining employment and as part...</p>
    <div class="more">READ MORE</div>
  </article>
  <article class="abs card" style="left:840px">
    <div class="date">25<small>JAN</small></div>
    <div class="thumb" role="img" aria-label="Photo of a stethoscope lying on a medical chart" style="background:linear-gradient(135deg,#dfeaf4,#7ea6c8)"></div>
    <h3>Lorem Ipsum is simply dummy text of the printinG.</h3>
    <p>The Ashford Medical Receptionist Training program is geared towards gaining employment and as part...</p>
    <div class="more">READ MORE</div>
  </article>
</section>

<section class="testimonials" role="img" aria-label="Faded photo of smiling office workers behind the testimonial">
  <h2 class="abs panel-title">TESTIMONIALS</h2>
  <div class="abs title-rule"></div>
  <div class="abs quote-mark">&ldquo;</div>
  <p class="abs quote-text">There are many variations of passages of Lorem Ipsum available, but the majority have suffered alteration in some form, by injected humour, or randomised words which don't look even slightly believable. If you are going to use a passage of Lorem Ipsum, you need to be sure there isn't anything embarrassing hidden in the middle of text. All the Lorem Ipsum generators on the Internet tend to repeat predefined chunks as necessary, making this the first true generator.</p>
  <svg class="abs" style="left:470px;top:258px" width="14" height="18" viewBox="0 0 14 18"><path d="M10 2 L3 9 L10 16" fill="none" stroke="#fff" stroke-width="2.6"/></svg>
  <div class="abs author" style="left:512px">
    <div class="avatar" role="img" aria-label="Portrait photo of the reviewer"></div>
    <div><b>DANIEL MORENO</b><small>Australia</small></div>
  </div>
  <svg class="abs" style="left:720px;top:258px" width="14" height="18" viewBox="0 0 14 18"><path d="M4 2 L11 9 L4 16" fill="none" stroke="#fff" stroke-width="2.6"/></svg>
</section>

<footer class="site-footer">
  <div class="abs f-logo">
    <div class="brand-name">ASHFORD INSTITUTE<br>OF TRAINING</div>
    <div class="brand-mark"></div>
  </div>
  <div class="abs f-divider"></div>
  <div class="abs f-contact">
    <h5>CONTACT US</h5>
    <div class="grp"><b>NEW SOUTH WALES, VICTORIA &amp; ACT</b>1800 555 201</div>
    <div class="grp"><b>SOUTH AUSTRALIA,&nbsp; QUEENSLAND, NT</b>1800 555 347</div>
    <div class="grp"><b>WESTERN AUSTRALIA</b>08 5550 4120</div>
  </div>
  <div class="abs f-enquiry">
    <h5>ENQUIRY</h5>
    <div class="f-field" style="top:32px">Name</div>
    <div class="f-field" style="top:74px">E mail</div>
    <div class="f-field" style="top:116px">Phone</div>
    <div class="f-msg">Message</div>
  </div>
  <div class="abs btn btn-submit">SUBMIT</div>
</footer>

<div class="abs bottom-bar" style="left:0;width:1200px">
  <div class="abs social"><span>Follow us on</span><i></i><i></i><i></i><i></i></div>
  <div class="abs copyright">Copyrights @ 2016 All Rights Reserved</div>
</div>

</body>
</html>
```